Professional & attention grabbing.

A business card design, front and back. I already have a logo I will attach, but I am open to something new as well.
Things to include:
Name:
Title:
Phone:
Email:
Wanting something that is professional but attention grabbing.
Also we do a lot of work using drones on natural gas pipelines (leading the future)if you want to include any of that. I'm open to ideas.
Target Market(s)
Natural gas transmission industry / greenhouse gas mitigation industry
Industry/Entity Type
Business
Colors
Designer to choose colors to be used in the design.
Look and feel
Each slider illustrates characteristics of the customer's brand and the style your logo design should communicate.

```html
<!DOCTYPE html>
<html lang="en">
<head>
<meta charset="utf-8">
<title>Vantor Line Inspections – Business Card</title>
<link rel="stylesheet" href="https://fonts.googleapis.com/css2?family=Lato:wght@400;700&display=swap">
<style>
  :root {
    --bg: #e9e7e3;
    --card-white: #ffffff;
    --card-dark: #3a3a3d;
    --accent-red: #c4202a;
    --text-light: #f2f2f2;
    --text-grey: #5a5a5d;
  }
  * { box-sizing: border-box; margin: 0; padding: 0; }
  html, body {
    width: 1200px; height: 950px; overflow: hidden;
    background: var(--bg);
    font-family: "Lato", Arial, sans-serif;
  }
  .sheet {
    width: 1200px; height: 950px;
    display: flex; flex-direction: column;
    align-items: center; justify-content: center; gap: 30px;
  }
  .card {
    position: relative;
    width: 760px; height: 434px;
    border-radius: 22px;
    overflow: hidden;
    box-shadow: 0 6px 18px rgba(0,0,0,0.18);
  }
  /* Front */
  .card--front { background: var(--card-white); }
  .front-wave { position: absolute; inset: 0; }
  .wave-red { fill: var(--accent-red); }
  .wave-dark { fill: var(--card-dark); }
  .brand {
    position: absolute; left: 48px; bottom: 70px;
    display: flex; align-items: center; gap: 14px;
  }
  .brand-mark { width: 34px; height: 34px; background: var(--accent-red); }
  .brand-name {
    font-size: 26px; font-weight: 700; color: var(--text-grey);
    letter-spacing: 0.5px;
  }
  .contact {
    position: absolute; right: 34px; top: 70px;
    text-align: right; color: var(--text-light);
  }
  .contact-name {
    font-size: 28px; font-weight: 700; color: var(--accent-red);
    letter-spacing: 2px; text-transform: uppercase;
  }
  .contact-title {
    font-size: 20px; letter-spacing: 1px; margin-top: 4px; margin-right: 30px;
  }
  .contact-list { list-style: none; margin-top: 26px; }
  .contact-item {
    display: flex; justify-content: flex-end; align-items: center; gap: 12px;
    font-size: 18px; letter-spacing: 0.6px; line-height: 32px;
  }
  .contact-icon { width: 16px; height: 16px; fill: var(--accent-red); flex: none; }
  .contact-item--plain { padding-right: 28px; }
  /* Back */
  .card--back { background: var(--card-dark); }
  .back-web {
    position: absolute; left: 40px; top: 50%;
    transform: translate(-50%, -50%) rotate(90deg);
    transform-origin: center;
    margin-left: 10px;
    color: var(--text-light); font-size: 16px; letter-spacing: 5px;
    white-space: nowrap;
  }
  .back-brand {
    position: absolute; inset: 0;
    display: flex; flex-direction: column; align-items: center; justify-content: center; gap: 22px;
  }
  .back-mark { width: 70px; height: 70px; background: var(--accent-red); }
  .back-name {
    font-size: 34px; font-weight: 700; color: var(--card-white); letter-spacing: 1px;
  }
</style>
</head>
<body>
<main class="sheet">
  <section class="card card--front" aria-label="Card front">
    <svg class="front-wave" viewBox="0 0 760 434" preserveAspectRatio="none" aria-hidden="true">
      <path class="wave-red" d="M398,0 C495,60 445,200 495,300 C522,360 545,400 572,434 L760,434 L760,0 Z"/>
      <path class="wave-dark" d="M422,0 C518,60 468,200 518,300 C545,360 566,400 594,434 L760,434 L760,0 Z"/>
    </svg>

    <div class="brand">
      <span class="brand-mark"></span>
      <span class="brand-name">Vantor Line Inspections</span>
    </div>

    <div class="contact">
      <p class="contact-name">Daniel Mercer</p>
      <p class="contact-title">CEO/FOUNDER</p>
      <ul class="contact-list">
        <li class="contact-item">555 210 4873
          <svg class="contact-icon" viewBox="0 0 16 16" aria-hidden="true"><path d="M3.5 1.5l2.5 0 1 3.5-1.6 1.1c.8 1.8 2.2 3.2 4 4l1.1-1.6 3.5 1v2.5c0 .8-.7 1.5-1.5 1.5C7 13.5 2 8.5 2 3c0-.8.7-1.5 1.5-1.5z"/></svg>
        </li>
        <li class="contact-item">daniel@vantorline.com
          <svg class="contact-icon" viewBox="0 0 16 16" aria-hidden="true"><path d="M1 3h14v10H1z M1.5 3.5L8 9l6.5-5.5" fill="var(--accent-red)" stroke="var(--card-dark)" stroke-width="1.2"/></svg>
        </li>
        <li class="contact-item">www.vantorline.com
          <svg class="contact-icon" viewBox="0 0 16 16" aria-hidden="true"><circle cx="8" cy="8" r="7"/><path d="M1 8h14M8 1c3 3.5 3 10.5 0 14M8 1c-3 3.5-3 10.5 0 14" fill="none" stroke="var(--card-dark)" stroke-width="1"/></svg>
        </li>
      </ul>
    </div>
  </section>

  <section class="card card--back" aria-label="Card back">
    <p class="back-web">www.vantorline.com</p>
    <div class="back-brand">
      <span class="back-mark"></span>
      <span class="back-name">Vantor Line Inspections</span>
    </div>
  </section>
</main>
</body>
</html>
```